New Business card design to reflect rebrand

I would like a business card design with a good base colour for our new logo and also a placeholder for a profile pic of the card holder. the design needs to be editable to the point that we can easily change the picture of the person and use that design for printmerlo etc. we are looking at a metalic finish business card so will need a good base colour to bring out the finish.

Target Market(s)

prospective customers

Industry/Entity Type

Business

Contact Information for Business Card

I would like one editable design that we can change the name of the card holder and profile picture. The design need to be in a format that be send to printmerlo etc.

Our address is Fenwick Lodge, Copse Lane, Ashcombe Vale, GU14 3TP Tel no. 01483 556172

Requirements
Must have
• place holder for a profile pic for the card holder. in AI or preferably PSD format

```html
<!DOCTYPE html>
<html lang="en">
<head>
<meta charset="utf-8">
<title>Corvane Workplace Services – Business Card</title>
<link href="https://fonts.googleapis.com/css2?family=Roboto:wght@400;500;700&display=swap" rel="stylesheet">
<style>
  :root {
    --backdrop: #e6e8eb;
    --card-white: #ffffff;
    --slate: #3f5570;
    --orange: #ef6a12;
    --ink: #444a52;
    --photo-grey: #b9bcbf;
    --photo-light: #d9dbdd;
  }
  * { margin: 0; padding: 0; box-sizing: border-box; }
  html, body {
    width: 1200px;
    height: 987px;
    overflow: hidden;
    background: var(--backdrop);
    font-family: "Roboto", Arial, sans-serif;
  }
  .card {
    position: absolute;
    left: 293px;
    width: 615px;
    height: 352px;
    box-shadow: 0 3px 10px rgba(0,0,0,0.18);
  }
  .card-front { top: 130px; background: var(--card-white); }
  .card-back { top: 505px; background: var(--slate); }

  .brand {
    position: absolute;
    display: flex;
    align-items: center;
    gap: 12px;
  }
  .brand-mark {
    width: 18px;
    height: 18px;
    background: var(--orange);
    flex: none;
  }
  .brand-name {
    font-weight: 700;
    line-height: 1.15;
    letter-spacing: 1.5px;
    text-transform: uppercase;
  }
  .card-front .brand { left: 43px; top: 70px; }
  .card-front .brand-name { color: var(--slate); font-size: 30px; }
  .card-front .brand-name small { display: block; font-size: 16px; letter-spacing: 3px; }

  .address {
    position: absolute;
    left: 45px;
    top: 207px;
    font-size: 16px;
    line-height: 23px;
    color: var(--ink);
  }
  .address .tel { margin-top: 4px; }

  .profile-photo {
    position: absolute;
    left: 430px;
    top: 58px;
    width: 128px;
    height: 159px;
    border-radius: 7px;
    background: linear-gradient(180deg, var(--photo-light) 0%, var(--photo-grey) 100%);
  }
  .holder {
    position: absolute;
    right: 57px;
    top: 229px;
    text-align: right;
  }
  .holder-name {
    font-size: 21px;
    font-weight: 700;
    color: var(--slate);
    letter-spacing: 0.5px;
  }
  .holder-role {
    margin-top: 6px;
    font-size: 16px;
    color: var(--orange);
  }

  .accent-line {
    position: absolute;
    left: 0; right: 0;
    top: 321px;
    height: 2px;
    background: var(--orange);
  }
  .footer-band {
    position: absolute;
    left: 0; right: 0;
    bottom: 0;
    height: 25px;
    background: var(--slate);
  }

  .card-back .brand {
    left: 50%;
    top: 50%;
    transform: translate(-50%, -50%);
  }
  .card-back .brand-name { color: var(--card-white); font-size: 34px; text-align: left; }
  .card-back .brand-name small { display: block; font-size: 18px; letter-spacing: 3.5px; }
</style>
</head>
<body>
  <section class="card card-front">
    <div class="brand">
      <span class="brand-mark"></span>
      <p class="brand-name">Corvane<small>Workplace Services</small></p>
    </div>
    <address class="address" style="font-style: normal;">
      <p>Fenwick Lodge</p>
      <p>Copse Lane, Ashcombe Vale, GU14 3TP</p>
      <p class="tel">Tel : 01483 556172</p>
    </address>
    <div class="profile-photo" role="img" aria-label="Profile photo of the card holder"></div>
    <div class="holder">
      <p class="holder-name">ALEX MARLOW</p>
      <p class="holder-role">CEO/FOUNDER</p>
    </div>
    <div class="accent-line"></div>
    <div class="footer-band"></div>
  </section>

  <section class="card card-back">
    <div class="brand">
      <span class="brand-mark"></span>
      <p class="brand-name">Corvane<small>Workplace Services</small></p>
    </div>
  </section>
</body>
</html>
```